NEW Wordpress Website Design for a Dynamic Long Term Healthcare Company in Hawaii

I would like a new website design for my current company, Marlow Health Collective, which has two different brands - Marlow Homecare and Marlow Senior Living. You can see the current website at www.marlowhealth-example.com. The website should be built using Wordpress Software and the Framewise theme. The website should have a local Hawaii island/tropical feel, but look professional for healthcare. I'm looking for something fresh, and want the designer to select colors, styles, etc.

In the Header, on all pages, I would like a menu that includes Home Care, Senior Living, Rates, and About Us.
Under each of the Header Menu Titles, I would like these drop downs included:
Home Care (drop down pages)- Nurse Aide Care, 24-Hour Home Care, Skilled Nursing, Lifestyle Aide, Hospice at Home, Bathing & Meal Service.
Senior Living (drop down pages) - Long-Term Stay, Short-Term Stay.
Rates (drop down page) - Rates.
About Us (drop down pages) - Our Mission, Ohana Talk, About Dana Marlow.

In the footer, on all pages, you should include the address: 248 Pueo Lane, Suite 310, Honolulu, HI 96817. Phone number: 808-555-0172
The footer should also include buttons for a page called Learn, Caregiver Jobs, and each of the service page links to include: Nurse Aide Care, 24-Hour Home Care, Skilled Nursing, Lifestyle Aide, Hospice at Home, Bathing & Meal Service.
Please don't take the current website and redesign a few aspects. I'm looking for a completely different look and feel.

Target Market(s)

40-80 year olds

Industry/Entity Type

Long Term Healthcare

Coding

Coded - Design and coding required

Requirements
Should not have
• Our existing website as a template. We are looking for a complete redesign. Thank you.

```html
<!DOCTYPE html>
<html lang="en">
<head>
<meta charset="utf-8">
<title>Marlow Health Collective — Homecare &amp; Senior Living</title>
<link rel="stylesheet" href="https://fonts.googleapis.com/css2?family=Poppins:wght@400;500;600;700&family=Inter:wght@400;500;600&display=swap">
<style>
:root{
  --coral:#e8766b;
  --coral-soft:#fdeeea;
  --teal:#2f5e5a;
  --ink:#1f2a2c;
  --muted:#5d6668;
  --line:#d9dedd;
  --white:#ffffff;
  --hero-a:#5b4636;
  --hero-b:#a88a6a;
}
*{box-sizing:border-box;margin:0;padding:0}
html,body{width:1200px;height:3368px;overflow:hidden}
body{font-family:"Inter",sans-serif;color:var(--ink);background:var(--white);position:relative;font-size:14px;line-height:1.6}
h1,h2,h3,h4{font-family:"Poppins",sans-serif;color:var(--ink)}
a{color:inherit;text-decoration:none}

/* header */
.site-header{height:100px;display:flex;align-items:center;padding:0 60px;justify-content:space-between}
.brand{display:flex;align-items:center;gap:10px;font-family:"Poppins",sans-serif;font-weight:600;font-size:20px;color:var(--coral)}
.brand-mark{width:22px;height:22px;background:var(--coral);border-radius:4px}
.main-nav{display:flex;align-items:center;gap:52px;font-size:15px;font-weight:500}
.main-nav .drop::after{content:"▾";font-size:11px;margin-left:6px;color:var(--muted)}
.btn-contact{background:var(--coral);color:var(--white);padding:12px 22px;border-radius:6px;font-size:14px;font-weight:500}

/* hero */
.hero{position:absolute;top:140px;left:60px;width:1080px;height:708px;border-radius:40px;overflow:hidden}
.hero-photo{position:absolute;inset:0;background:linear-gradient(135deg,var(--hero-a) 0%,var(--hero-b) 55%,#d9c6a6 100%)}
.hero-shade{position:absolute;inset:0;background:rgba(20,14,10,.32)}
.hero-copy{position:absolute;top:240px;left:0;right:0;text-align:center;color:var(--white)}
.hero-copy h1{color:var(--white);font-size:58px;font-weight:600;line-height:1.18}
.hero-copy p{margin:26px auto 0;width:760px;font-size:13px;line-height:1.55;opacity:.92}

/* services */
.services{position:absolute;top:892px;left:60px;width:1080px}
.eyebrow{color:var(--coral);font-size:14px;font-weight:500;margin-bottom:8px}
.section-head{display:flex;justify-content:space-between}
.section-head h2{font-size:34px;font-weight:600;line-height:1.2;width:440px}
.section-head p{width:540px;font-size:14px;color:var(--muted);margin-top:6px}
.card-grid{margin-top:44px;display:grid;grid-template-columns:repeat(3,360px);grid-auto-rows:290px}
.card{padding:32px 30px}
.card.is-featured{background:var(--coral-soft)}
.card-icon{width:40px;height:40px;border-radius:50%;background:#eef0ef;display:flex;align-items:center;justify-content:center;margin-bottom:22px}
.card.is-featured .card-icon{background:var(--teal)}
.card h3{font-size:18px;font-weight:500;margin-bottom:12px}
.card p{font-size:13px;color:var(--muted);line-height:1.55}
.card .arrow{display:block;margin-top:16px;font-size:18px}

/* senior living */
.senior{position:absolute;top:1652px;left:60px;width:1080px}
.senior h2{font-size:34px;font-weight:600}
.stay-row{position:absolute;left:0;width:1080px}
.stay-text{position:absolute;width:500px}
.stay-text h3{font-size:15px;font-weight:600;margin-bottom:18px}
.stay-text p{font-size:13px;color:var(--muted);line-height:1.65}
.stay-text .read{display:inline-block;margin-top:22px;font-size:13px;font-weight:600}
.photo-block{position:absolute;border-radius:4px}
.photo-long{background:linear-gradient(135deg,#7a5e4a,#c7a585 60%,#9fb4a8)}
.photo-short{background:linear-gradient(135deg,#6d5a48,#b89472 55%,#e0d2bb)}

/* contact */
.contact{position:absolute;top:2460px;left:0;width:1200px;height:560px;background:var(--coral-soft)}
.contact-photo{position:absolute;left:0;top:0;width:652px;height:560px;background:linear-gradient(150deg,#5c3a2a,#a8735a 50%,#d6b896)}
.contact-body{position:absolute;left:672px;top:36px;width:440px}
.contact-body h2{font-size:36px;font-weight:600;line-height:1.18;margin-top:4px}
.contact-body .lede{font-size:13px;color:var(--muted);margin-top:14px}
.form{margin-top:26px;display:grid;grid-template-columns:1fr 1fr;gap:14px}
.field{grid-column:span 2;height:38px;border:1px solid #c9cfcd;border-radius:20px;background:var(--white);padding:0 18px;display:flex;align-items:center;justify-content:space-between;font-size:12px;color:#8a9292}
.field.half{grid-column:span 1}
.submit{grid-column:span 2;height:40px;border-radius:20px;background:var(--teal);color:var(--white);display:flex;align-items:center;justify-content:center;font-weight:600;font-size:13px;letter-spacing:.03em}

/* footer */
.site-footer{position:absolute;top:3080px;left:60px;width:1080px;height:240px;display:flex}
.footer-about{width:408px}
.footer-about p{font-size:13px;color:var(--muted);margin-top:18px;width:250px;line-height:1.55}
.footer-col{width:212px}
.footer-col h4,.footer-contact h4{font-size:14px;font-weight:600;margin-bottom:12px}
.footer-col li{list-style:none;font-size:13px;color:var(--muted);margin-bottom:6px}
.footer-contact{width:188px;font-size:13px;color:var(--muted)}
.footer-contact .phone{font-weight:600;color:var(--ink);font-size:14px}
.socials{display:flex;gap:10px;margin-top:8px}
.socials span{width:24px;height:24px;border-radius:50%;background:var(--ink)}
.copyright{position:absolute;top:3330px;left:60px;width:1080px;border-top:1px solid var(--line);padding-top:10px;text-align:center;font-size:12px;color:var(--muted)}
</style>
</head>
<body>

<header class="site-header">
  <a class="brand" href="#"><span class="brand-mark"></span>Marlow Health Collective</a>
  <nav class="main-nav">
    <a class="drop" href="#">Home Care</a>
    <a class="drop" href="#">Senior Living</a>
    <a href="#">Rates</a>
    <a class="drop" href="#">About Us</a>
    <a class="btn-contact" href="#">Contact Us</a>
  </nav>
</header>

<section class="hero">
  <div class="hero-photo" role="img" aria-label="Caregiver assisting an elderly resident in a warm, sunlit living room"></div>
  <div class="hero-shade"></div>
  <div class="hero-copy">
    <h1>Hawaii's Choice<br>Homecare &amp; Senior Living</h1>
    <p>Marlow Health Collective provides caring, professional in-home support and senior living throughout the islands, helping every family stay close, comfortable and well looked after in the spirit of aloha.</p>
  </div>
</section>

<section class="services">
  <div class="section-head">
    <div>
      <div class="eyebrow">Marlow Homecare</div>
      <h2>Marlow Homecare Services Overview</h2>
    </div>
    <p>Marlow Homecare is a leading provider of compassionate and professional homecare services. With a deep commitment to enhancing the quality of life for individuals of all ages, our company is dedicated to delivering personalized care in the comfort of our clients' homes.</p>
  </div>
  <div class="card-grid">
    <article class="card">
      <div class="card-icon"><svg width="18" height="18" viewBox="0 0 24 24" fill="none" stroke="#1f2a2c" stroke-width="2"><path d="M3 11l9-7 9 7v9H3z"/><path d="M10 20v-5h4v5"/></svg></div>
      <h3>Nurse Aide Care</h3>
      <p>Nurse aide care, also known as personal care or non-medical care, involves assisting individuals with their daily activities, such as bathing, dressing, grooming, toileting, and mobility.</p>
      <span class="arrow">→</span>
    </article>
    <article class="card">
      <div class="card-icon"><svg width="18" height="18" viewBox="0 0 24 24" fill="none" stroke="#1f2a2c" stroke-width="2"><path d="M3 11l9-7 9 7v9H3z"/><path d="M10 20v-5h4v5"/></svg></div>
      <h3>24-Hour Home Care</h3>
      <p>Skilled nursing services are provided by licensed nurses, often Registered Nurses (RNs) or Licensed Practical Nurses (LPNs).</p>
      <span class="arrow">→</span>
    </article>
    <article class="card is-featured">
      <div class="card-icon"><svg width="18" height="18" viewBox="0 0 24 24" fill="none" stroke="#ffffff" stroke-width="2"><path d="M3 11l9-7 9 7v9H3z"/><path d="M10 20v-5h4v5"/></svg></div>
      <h3>Skilled Nursing</h3>
      <p>Skilled nursing services are provided by licensed nurses, often Registered Nurses (RNs) or Licensed Practical Nurses (LPNs).</p>
    </article>
    <article class="card">
      <div class="card-icon"><svg width="18" height="18" viewBox="0 0 24 24" fill="none" stroke="#1f2a2c" stroke-width="2"><path d="M3 11l9-7 9 7v9H3z"/><path d="M10 20v-5h4v5"/></svg></div>
      <h3>Lifestyle Aide</h3>
      <p>Lifestyle aid services focus on enhancing the overall quality of life for individuals. This can include assistance with recreational activities, hobbies, exercise, and transportation to social events or appointments.</p>
      <span class="arrow">→</span>
    </article>
    <article class="card">
      <div class="card-icon"><svg width="18" height="18" viewBox="0 0 24 24" fill="none" stroke="#1f2a2c" stroke-width="2"><path d="M3 11l9-7 9 7v9H3z"/><path d="M10 20v-5h4v5"/></svg></div>
      <h3>Hospice at Home</h3>
      <p>Hospice care is designed for individuals with advanced or terminal illnesses. It focuses on providing comfort, pain management, emotional support, and assistance with daily activities.</p>
      <span class="arrow">→</span>
    </article>
    <article class="card">
      <div class="card-icon"><svg width="18" height="18" viewBox="0 0 24 24" fill="none" stroke="#1f2a2c" stroke-width="2"><path d="M3 11l9-7 9 7v9H3z"/><path d="M10 20v-5h4v5"/></svg></div>
      <h3>Bathing &amp; Meal Service</h3>
      <p>Bathing service involves assisting individuals with personal hygiene, including bathing and grooming.</p>
    </article>
  </div>
</section>

<section class="senior">
  <div class="eyebrow">Marlow Senior Living</div>
  <h2>Supportive Environment Addresses The Unique</h2>

  <div class="stay-row" style="top:108px">
    <div class="stay-text" style="left:0;top:40px">
      <h3>Long-Term Stay</h3>
      <p>A trusted and welcoming home for residents who need ongoing support. For more than 25 years our island team has cared for kupuna with patience and warmth. From restful mornings and shared meals to gentle activities, every day is planned around each resident's routine. Our staff know every name, every story and every preference, and families are always welcome to visit, share a meal and take part in daily life.</p>
      <a class="read" href="#">Read More ›</a>
    </div>
    <div class="photo-block photo-long" style="left:548px;top:0;width:532px;height:300px" role="img" aria-label="Residents and caregivers gathered together in a bright senior living lounge"></div>
  </div>

  <div class="stay-row" style="top:448px">
    <div class="photo-block photo-short" style="left:0;top:0;width:532px;height:300px" role="img" aria-label="Comfortable private resident bedroom with a made bed and warm lamps"></div>
    <div class="stay-text" style="left:572px;top:40px">
      <h3>Short-Term Stay</h3>
      <p>A restful and caring place to recover after a hospital visit or to give family caregivers a well-earned break. For more than 25 years our island team has welcomed guests for stays of days or weeks. Each guest receives a personal care plan, daily support and friendly company, with nurses on hand around the clock so every family can relax knowing loved ones are safe, comfortable and cared for.</p>
      <a class="read" href="#">Read More ›</a>
    </div>
  </div>
</section>

<section class="contact">
  <div class="contact-photo" role="img" aria-label="Caregiver serving a meal to a seated elderly man at home"></div>
  <div class="contact-body">
    <div class="eyebrow">Contact Us</div>
    <h2>Call Us Today or You Can Fill Out the Form</h2>
    <p class="lede">Call us today or you can fill out the form below and someone will be in touch shortly.</p>
    <div class="form">
      <div class="field">Name</div>
      <div class="field half">Email</div>
      <div class="field half">Phone</div>
      <div class="field">How can we help? <span>▾</span></div>
      <div class="field">Questions/Comments</div>
      <div class="field">How did you hear about us? <span>▾</span></div>
      <div class="submit">SUBMIT</div>
    </div>
  </div>
</section>

<footer class="site-footer">
  <div class="footer-about">
    <a class="brand" href="#"><span class="brand-mark"></span>Marlow Health Collective</a>
    <p>Marlow Health Collective – Marlow Homecare is a leading provider of compassionate and professional homecare services. With a deep commitment to enhancing the quality of life for individuals of all ages.</p>
  </div>
  <div class="footer-col">
    <h4>Services</h4>
    <ul><li>Learn</li><li>Caregiver Jobs</li></ul>
  </div>
  <div class="footer-col" style="width:272px">
    <h4>Homecare</h4>
    <ul><li>Nurse Aide Care</li><li>24-Hour Home Care</li><li>Skilled Nursing</li><li>Lifestyle Aide</li><li>Hospice at Home</li><li>Bathing &amp; Meal Service</li></ul>
  </div>
  <div class="footer-contact">
    <div class="phone">808-555-0172</div>
    <p style="margin-top:8px">248 Pueo Lane, Suite 310,<br>Honolulu, HI 96817</p>
    <h4 style="margin-top:18px;margin-bottom:4px">Social Media</h4>
    <div class="socials"><span></span><span></span></div>
  </div>
</footer>
<div class="copyright">© 2024 Marlow Health Collective. All Rights Reserved.</div>

</body>
</html>
```